Web page for a garment manufacturing company

We are clothing manufacturer based in Romania.
With our recent expansion, we have significantly increased our internal capacity, allowing us to take on new partnerships and deliver high-quality production services.
Our expertise includes producing classic coats, blazers, trousers, skirts, dresses, and blouses, though we are flexible and open to working with various other textile products.

Target Market(s)

High-end market and luxury

Industry/Entity Type

Garments Manufacturer

Coding

Coded - Design and coding required

Number of Pages Required

1 page

Colors

Designer to choose only greyscale colors for use in the design.

Requirements
Must have
• Velmora logo from our presentation
Nice to have
• https://www.lorvani.pt/
Should not have
• prices, wedding dresses, collections

```html
<!DOCTYPE html>
<html lang="en">
<head>
<meta charset="utf-8">
<title>Velmora — Garment Manufacturing</title>
<link href="https://fonts.googleapis.com/css2?family=Inter:wght@300;400;500&display=swap" rel="stylesheet">
<style>
:root{
  --ink:#232323;
  --ink-soft:#2d2d2d;
  --white:#ffffff;
  --muted:#bdbdbd;
  --dim:#7a7a7a;
  --line:rgba(255,255,255,.55);
  --card-line:#4d4d4d;
  --tone-1:#e2e2e2;
  --tone-2:#a9a9a9;
  --tone-3:#6e6e6e;
  --tone-4:#454545;
  --tone-5:#2f2f2f;
}
*{box-sizing:border-box;margin:0;padding:0}
html,body{width:1200px;height:3938px;overflow:hidden}
body{background:var(--ink);color:var(--white);font-family:"Inter",sans-serif;position:relative}
.abs{position:absolute}
.btn{display:inline-flex;align-items:center;gap:14px;border:1px solid var(--white);border-radius:6px;padding:0 20px;height:36px;font-size:14px;color:var(--white);text-decoration:none;white-space:nowrap}
.btn svg{width:8px;height:10px}

/* header */
.site-header{top:0;left:0;width:1200px;height:80px;background:var(--ink)}
.brand{left:60px;top:14px;font-size:42px;font-weight:300;letter-spacing:-1px}
.nav{left:322px;top:31px;display:flex;gap:34px;font-size:14px;letter-spacing:.3px}
.lang{left:928px;top:31px;font-size:14px;display:flex;gap:14px}
.lang .off{color:var(--dim);border-left:1px solid var(--dim);padding-left:14px}
.contact-btn{left:1029px;top:19px;height:40px;padding:0 20px}

/* photo areas */
.photo{position:absolute}
.hero{top:80px;left:0;width:1200px;height:605px;background:linear-gradient(180deg,#4f4f4f 0%,#5e5e5e 35%,#6a6a6a 60%,#545454 100%)}
.hero-title{left:60px;top:488px;font-size:46px;font-weight:300;line-height:50px}
.hero-more{left:60px;top:604px;font-size:13px;line-height:16px}
.about{top:685px;left:0;width:1200px;height:472px;background:linear-gradient(135deg,#3a3a3a,#4a4a4a 50%,#363636)}
.about-title{left:43px;top:866px;font-size:33px;font-weight:300}
.about-btn{left:43px;top:941px;height:34px;font-size:13px}
.about-copy{left:608px;top:852px;width:428px;font-size:13.4px;line-height:20px}

/* feature bands */
.band{left:0;width:1200px;height:484px;background:var(--ink-soft)}
.band .img{position:absolute;width:600px;height:484px;top:0}
.band .txt{position:absolute;top:0;width:600px;height:484px;padding:86px 0 0 100px}
.eyebrow{font-size:13px;color:var(--muted);letter-spacing:.5px}
.band h3{font-size:33px;font-weight:300;line-height:40px;margin-top:34px}
.band p{font-size:13.4px;line-height:20px;width:356px;margin-top:28px}
.band .btn{margin-top:32px;height:34px;font-size:13px}

/* contact form */
.journey{top:2608px;left:0;width:1200px;height:484px;background:linear-gradient(180deg,#4c4c4c,#5d5d5d 60%,#3a3a3a)}
.journey-title{top:2694px;left:0;width:1200px;text-align:center;font-size:33px;font-weight:300}
.journey-sub{top:2747px;left:0;width:1200px;text-align:center;font-size:13px}
.field{left:428px;width:344px;border-bottom:1px solid var(--line);font-size:13px;padding:0 0 6px 20px}
.submit{left:428px;top:2974px;width:344px;height:32px;background:var(--white);color:var(--ink);font-size:13px;display:flex;align-items:center;justify-content:center}

/* insights */
.insight-title{left:212px;top:3146px;font-size:33px;font-weight:300}
.view-more{left:859px;top:3146px;height:38px;padding:0 22px}
.card{top:3211px;width:241px;height:446px;border:1px solid var(--card-line)}
.card .img{height:240px}
.card .meta{padding:24px 16px 0;font-size:10px;color:var(--muted);line-height:20px}
.card h4{padding:8px 18px 0;font-size:16px;font-weight:400;line-height:24px}
.card p{padding:14px 20px 0;font-size:11px;line-height:17px;color:var(--muted)}

/* footer */
.foot-brand{left:86px;top:3744px;font-size:44px;font-weight:300;letter-spacing:-1px}
.foot-addr{left:86px;top:3812px;font-size:12px;line-height:20px}
.foot-addr span{text-decoration:underline}
.col{top:3754px;font-size:11px;line-height:24px}
.col b{font-weight:400;font-size:12px;display:block;margin-bottom:6px}
.news{left:855px;top:3754px;font-size:11px}
.news small{display:block;font-size:8px;margin-top:6px}
.news-form{left:855px;top:3799px;width:258px;height:34px;border:1px solid var(--white);display:flex}
.news-form .in{flex:1;background:var(--white);color:var(--dim);font-size:10px;padding:11px 16px}
.news-form .go{width:76px;display:flex;align-items:center;justify-content:center;font-size:12px}
.rule{left:86px;top:3884px;width:1027px;border-top:1px solid var(--card-line)}
.legal{top:3900px;font-size:9px;color:var(--muted)}
</style>
</head>
<body>
<header class="abs site-header">
  <div class="abs brand">Velmora</div>
  <nav class="abs nav"><span>ABOUT US</span><span>PRODUCT</span><span>CONCEPTS</span><span>INSIGHTS</span><span>COMPANY</span></nav>
  <div class="abs lang"><span>EN</span><span class="off">RO</span></div>
  <a class="abs btn contact-btn">Contact Us</a>
</header>

<section class="photo hero" role="img" aria-label="Brick factory building exterior at dusk"></section>
<h1 class="abs hero-title">WHERE FASHION<br>MEET QUALITY</h1>
<div class="abs hero-more">View more<br><svg width="8" height="6" viewBox="0 0 8 6"><path d="M1 1l3 3 3-3" stroke="#fff" fill="none"/></svg></div>

<section class="photo about" role="img" aria-label="Aerial view of the factory campus with solar roofs"></section>
<h2 class="abs about-title">VELMORA Brastova</h2>
<a class="abs btn about-btn">Read More <svg viewBox="0 0 8 10"><path d="M2 1l4 4-4 4" stroke="#fff" fill="none"/></svg></a>
<p class="abs about-copy">VELMORA is a manufacturing company for Ready-to-wear, situated in Brastova, a city with a rich tradition in the clothing industry. The top management is international, and we are proud to have a diverse and dynamic group of professionals from different countries working together. With our optimistic team spirit and passion for high-quality productions, we are ready to take on new challenges and delight our clients with very good results.</p>

<section class="abs band" style="top:1157px">
  <div class="img" style="left:0;background:linear-gradient(160deg,var(--tone-1),var(--tone-2) 55%,var(--tone-3))" role="img" aria-label="Garment warehouse with rails of hanging clothes"></div>
  <div class="txt" style="left:600px">
    <div class="eyebrow">PRODUCT</div>
    <h3>HIGH-QUALITY<br>PRODUCTS<br>AND SERVICES</h3>
    <p>Continuously improveour products and services, focusing on exceptional quality, durability, and customer satisfaction.A</p>
    <a class="btn">Explore More <svg viewBox="0 0 8 10"><path d="M2 1l4 4-4 4" stroke="#fff" fill="none"/></svg></a>
  </div>
</section>

<section class="abs band" style="top:1641px">
  <div class="txt" style="left:0">
    <div class="eyebrow">PEOPLE</div>
    <h3>PRIORITIZE WORKER<br>WELL-BEING</h3>
    <p>Implement policies and initiatives that support the physical and mental well-being of our workers, ensuringfair wages, safe working conditions, and opportunities for professional growth and personal development.</p>
    <a class="btn">Explore More <svg viewBox="0 0 8 10"><path d="M2 1l4 4-4 4" stroke="#fff" fill="none"/></svg></a>
  </div>
  <div class="img" style="left:600px;background:linear-gradient(120deg,var(--tone-2),var(--tone-1) 45%,var(--tone-4) 75%,var(--tone-1))" role="img" aria-label="Tailor measuring a garment on a cutting table"></div>
</section>

<section class="abs band" style="top:2125px">
  <div class="img" style="left:0;background:linear-gradient(150deg,var(--tone-1),var(--tone-3) 55%,var(--tone-5))" role="img" aria-label="Operator at an automated fabric cutting machine"></div>
  <div class="txt" style="left:600px">
    <div class="eyebrow">CONCEPTS</div>
    <h3>INNOVATION AND<br>TECHNOLOGY</h3>
    <p>Ø&nbsp; Embrace innovation and leverage technology to streamline operations, enhance customer experience, and develop sustainable solutions that addressevolving market demands.</p>
    <a class="btn">Explore More <svg viewBox="0 0 8 10"><path d="M2 1l4 4-4 4" stroke="#fff" fill="none"/></svg></a>
  </div>
</section>

<section class="photo journey" role="img" aria-label="Factory entrance with loading doors"></section>
<h2 class="abs journey-title">Start Your Custom Clothing Journey</h2>
<div class="abs journey-sub">Connect with us today to bring your designs to life with quality craftsmanship and dedicated service.</div>
<div class="abs field" style="top:2802px">Name</div>
<div class="abs field" style="top:2862px">Email</div>
<div class="abs field" style="top:2922px">Write your feedback</div>
<div class="abs submit">Submit</div>

<h2 class="abs insight-title">FEATURED INSIGHT</h2>
<a class="abs btn view-more">View More <svg viewBox="0 0 8 10"><path d="M2 1l4 4-4 4" stroke="#fff" fill="none"/></svg></a>
<article class="abs card" style="left:219px">
  <div class="img" style="background:linear-gradient(150deg,var(--tone-1),var(--tone-3))" role="img" aria-label="Technician operating a garment testing machine"></div>
  <div class="meta">2 days ago<br>Publications</div>
  <h4>Ethical Production Practices</h4>
  <p>Discover our commitment to fair labor, quality craftsmanship, and …</p>
</article>
<article class="abs card" style="left:480px">
  <div class="img" style="background:linear-gradient(150deg,var(--tone-3),var(--tone-5) 60%,var(--tone-2))" role="img" aria-label="Computer screens showing 3D garment design software"></div>
  <div class="meta">Oct 15<br>Publications</div>
  <h4>The Future of Fabric Technology</h4>
  <p>See how innovative materials are transforming comfort, durability …</p>
</article>
<article class="abs card" style="left:742px">
  <div class="img" style="background:linear-gradient(150deg,var(--tone-1),var(--tone-3) 60%,var(--tone-5))" role="img" aria-label="Worker inspecting a jacket on a hanger"></div>
  <div class="meta">Oct 8<br>Publications</div>
  <h4>Custom Clothing for Every Brand</h4>
  <p>Learn how our tailored approach helps brands create unique pieces …</p>
</article>

<footer>
  <div class="abs foot-brand">Velmora</div>
  <div class="abs foot-addr">ROMANIA, Brastova, Str. Livezii 8,<br>+40 300 555 018 - <span>info@velmorafashion.com</span></div>
  <div class="abs col" style="left:470px"><b>Quick Links</b>Home<br>Product<br>Consepts</div>
  <div class="abs col" style="left:662px"><b>Important Links</b>Contact Us<br>Inshigts<br>About Us<br>Company</div>
  <div class="abs news">Subscribe Our News<small>Get reviews, tips and more in your inbox!</small></div>
  <div class="abs news-form"><div class="in">What's your email?*</div><div class="go">Submit</div></div>
  <div class="abs rule"></div>
  <div class="abs legal" style="left:86px">© Halden Works. All Rights Reserved.</div>
  <div class="abs legal" style="left:934px">Privacy Policy</div>
  <div class="abs legal" style="left:1034px">Terms of Service</div>
</footer>
</body>
</html>
```